Mindfulness School for Children -- Business Cards

We're looking for business cards for our school directors and owners. We're a mindfulness school for children called little lanterns. Attached are our logos/icons.

```html
<!DOCTYPE html>
<html lang="en">
<head>
<meta charset="utf-8">
<title>little lanterns — Business Cards</title>
<link rel="stylesheet" href="https://fonts.googleapis.com/css2?family=Lustria&family=Questrial&family=Arimo:wght@400&display=swap">
<style>
  :root {
    --backdrop: #cfcfcf;
    --front-top: #76c4d9;
    --front-bottom: #6aae96;
    --paper: #ffffff;
    --brand-teal: #5aae9e;
    --name-green: #86c79a;
    --name-blue: #4aafc9;
    --ink: #4a4a4a;
    --icon-green: #86c79a;
    --link-blue: #4aafc9;
  }
  * { box-sizing: border-box; margin: 0; padding: 0; }
  html, body { width: 1200px; height: 900px; overflow: hidden; }
  body {
    background: var(--backdrop);
    display: flex;
    flex-direction: column;
    align-items: center;
    justify-content: center;
    gap: 44px;
  }
  .card {
    position: relative;
    width: 620px;
    height: 354px;
    border-radius: 26px;
    box-shadow: 0 10px 24px rgba(0,0,0,0.22);
    overflow: hidden;
  }
  .card--front {
    background: linear-gradient(180deg, var(--front-top) 0%, var(--front-bottom) 100%);
    display: flex;
    align-items: center;
    justify-content: center;
  }
  .wordmark {
    font-family: "Lustria", Georgia, serif;
    font-size: 52px;
    letter-spacing: 1px;
    color: var(--paper);
    display: flex;
    align-items: center;
    gap: 14px;
  }
  .wordmark__dot {
    width: 16px; height: 16px; border-radius: 50%;
    background: currentColor;
  }
  .card--back { background: var(--paper); }
  .card--back .wordmark {
    position: absolute;
    left: 54px; top: 92px;
    font-size: 44px;
    color: var(--brand-teal);
  }
  .person {
    position: absolute;
    left: 58px; top: 176px;
  }
  .person__name {
    font-family: "Questrial", "Century Gothic", sans-serif;
    font-size: 34px;
    line-height: 1.05;
  }
  .person__first { color: var(--name-green); }
  .person__last { color: var(--name-blue); }
  .person__role {
    font-family: "Arimo", Arial, sans-serif;
    font-size: 17px;
    color: var(--ink);
    margin-top: 2px;
  }
  .contacts {
    position: absolute;
    left: 58px; top: 256px;
    list-style: none;
    font-family: "Arimo", Arial, sans-serif;
    font-size: 16px;
    color: var(--ink);
  }
  .contacts li {
    display: flex; align-items: center; gap: 10px;
    height: 24px;
  }
  .contacts svg { width: 16px; height: 16px; flex: none; }
  .contacts .domain { color: var(--link-blue); }
  .address {
    position: absolute;
    right: 44px; top: 150px;
    text-align: right;
    font-family: "Arimo", Arial, sans-serif;
    font-size: 15px;
    line-height: 1.45;
    color: var(--ink);
  }
</style>
</head>
<body>

  <section class="card card--front" aria-label="Business card front">
    <div class="wordmark"><span class="wordmark__dot"></span>little lanterns</div>
  </section>

  <section class="card card--back" aria-label="Business card back">
    <div class="wordmark"><span class="wordmark__dot"></span>little lanterns</div>

    <div class="person">
      <p class="person__name"><span class="person__first">Daniel</span> <span class="person__last">Harper</span></p>
      <p class="person__role">Managing Director</p>
    </div>

    <ul class="contacts">
      <li>
        <svg viewBox="0 0 16 16" aria-hidden="true"><path d="M4 1.5l2.2 3-1.3 1.6c.8 1.9 2.4 3.5 4.3 4.3l1.6-1.3 3 2.2-1.3 2.5C7 14 2 9 1.5 2.8z" fill="var(--icon-green)"/></svg>
        <span>044-555 010 220</span>
      </li>
      <li>
        <svg viewBox="0 0 16 16" aria-hidden="true"><rect x="1" y="3.5" width="14" height="9" rx="1" fill="var(--icon-green)"/><path d="M1.5 4l6.5 5 6.5-5" stroke="#fff" stroke-width="1.2" fill="none"/></svg>
        <span>hello@littlelanterns.org</span>
      </li>
      <li>
        <svg viewBox="0 0 16 16" aria-hidden="true"><g fill="none" stroke="var(--icon-green)" stroke-width="1.3"><circle cx="8" cy="8" r="6.3"/><ellipse cx="8" cy="8" rx="2.8" ry="6.3"/><path d="M1.7 8h12.6M2.8 4.8h10.4M2.8 11.2h10.4"/></g></svg>
        <span>www.<span class="domain">littlelanterns</span>.org</span>
      </li>
    </ul>

    <address class="address">
      88, Willow Lane, Brookfield<br>
      20417, Meadowshire
    </address>
  </section>

</body>
</html>
```